Redesign of business card for Cedar Ridge Mechanical

We are looking for a new design for our business cards for Cedar Ridge Mechanical. We are a plumbing & HVAC construction company, operating on the West Coast of Canada and USA. Logo attached.
Industry/Entity Type
Construction - Plumbing & HVAC
Contact Information for Business Card
Name, address, phone numbers, email, website address
Look and feel
Each slider illustrates characteristics of the customer's brand and the style your logo design should communicate.

```html
<!DOCTYPE html>
<html lang="en">
<head>
<meta charset="utf-8">
<title>Cedar Ridge Mechanical – Business Card</title>
<link href="https://fonts.googleapis.com/css2?family=Montserrat:wght@400;700&display=swap" rel="stylesheet">
<style>
  :root {
    --stage: #232323;
    --card: #141414;
    --card-edge: #f2f2f2;
    --ink: #ffffff;
    --ink-soft: #e6e6e6;
    --pattern-light: #4a4a4a;
    --pattern-dark: #0c0c0c;
  }
  html, body {
    margin: 0;
    width: 1200px;
    height: 780px;
    overflow: hidden;
    background: var(--stage);
    font-family: "Montserrat", sans-serif;
  }
  .canvas {
    position: relative;
    width: 1200px;
    height: 780px;
  }
  .card {
    position: absolute;
    width: 560px;
    height: 320px;
    border-radius: 22px;
    background: var(--card);
    box-shadow: 0 0 0 2px var(--card-edge), 0 18px 40px rgba(0,0,0,.55);
    overflow: hidden;
    color: var(--ink);
  }
  .card--back { left: 60px; top: 50px; }
  .card--front { left: 580px; top: 410px; }

  .back-pattern {
    position: absolute;
    inset: 0;
    background: linear-gradient(100deg, var(--pattern-light) 0%, #262626 40%, var(--pattern-dark) 65%, #050505 100%);
  }
  .back-brand {
    position: absolute;
    right: 34px;
    bottom: 96px;
    display: flex;
    align-items: center;
    gap: 8px;
    font-weight: 700;
    font-size: 11px;
    letter-spacing: .04em;
    text-transform: uppercase;
  }
  .brand-square {
    width: 12px;
    height: 12px;
    border: 2px solid var(--ink);
    box-sizing: border-box;
  }

  .front-brand {
    position: absolute;
    left: 36px;
    top: 0;
    bottom: 0;
    width: 220px;
    display: flex;
    align-items: center;
    gap: 14px;
  }
  .front-brand .brand-square {
    width: 30px;
    height: 30px;
    border-width: 4px;
    flex: none;
  }
  .front-brand .brand-name {
    font-weight: 700;
    font-size: 22px;
    line-height: 1.15;
    text-transform: uppercase;
    letter-spacing: .02em;
  }
  .divider {
    position: absolute;
    left: 282px;
    top: 86px;
    width: 1.5px;
    height: 160px;
    background: var(--ink);
  }
  .contact {
    position: absolute;
    left: 306px;
    top: 78px;
    right: 20px;
  }
  .contact__name {
    margin: 0;
    font-weight: 700;
    font-size: 21px;
    letter-spacing: .02em;
  }
  .contact__role {
    margin: 2px 0 14px;
    font-size: 13px;
    color: var(--ink-soft);
  }
  .contact__address {
    margin: 0 0 14px;
    font-style: normal;
    font-size: 13px;
    line-height: 1.4;
    color: var(--ink-soft);
  }
  .contact__list {
    list-style: none;
    margin: 0;
    padding: 0;
    font-size: 12.5px;
    line-height: 1.65;
  }
  .contact__list li {
    display: flex;
    align-items: center;
    gap: 8px;
  }
  .contact__list svg {
    width: 11px;
    height: 11px;
    fill: var(--ink);
    flex: none;
  }
</style>
</head>
<body>
<main class="canvas">

  <section class="card card--back" aria-label="Card back">
    <div class="back-pattern" role="img" aria-label="Repeating monogram pattern in glossy black on black"></div>
    <div class="back-brand">
      <span class="brand-square"></span>
      <span class="brand-name">Cedar Ridge Mechanical</span>
    </div>
  </section>

  <section class="card card--front" aria-label="Card front">
    <div class="front-brand">
      <span class="brand-square"></span>
      <span class="brand-name">Cedar Ridge Mechanical</span>
    </div>

    <div class="divider"></div>

    <div class="contact">
      <h1 class="contact__name">DANIEL HART</h1>
      <p class="contact__role">Managing Director</p>
      <address class="contact__address">Your address, City<br>State, Zip 1234</address>
      <ul class="contact__list">
        <li>
          <svg viewBox="0 0 16 16" aria-hidden="true"><path d="M3.5 1l2.5 3-1.5 2c1 2 2.5 3.5 4.5 4.5l2-1.5 3 2.5-1.5 3C6 14 2 10 1 3.5z"/></svg>
          604 555 0182
        </li>
        <li>
          <svg viewBox="0 0 16 16" aria-hidden="true"><path d="M1 3h14v10H1z M2.5 4.5v.3L8 9l5.5-4.2v-.3z" fill-rule="evenodd"/></svg>
          info@cedarridgemech.com
        </li>
        <li>
          <svg viewBox="0 0 16 16" aria-hidden="true"><circle cx="8" cy="8" r="7"/></svg>
          www.cedarridgemech.com
        </li>
      </ul>
    </div>
  </section>

</main>
</body>
</html>
```